Computer Company needs a Business card design

We need a business card design for our business. We assist people to transition to the KVS (Kestrel Vantage Scheme). The Verandal Crown Office-owned kvs™ network is a brand new telecommunications network currently being rolled out across Australia, giving access to a reliable broadband connection. Our niche market will predominantly be domestic customers in the 50+ age bracket. The assistance that we provide is everything from arranging the equipment, arranging the plan and contract term, appointment times, final testing of the network and any tweaks that need to be made. We basically PM the transition from start to finish. The business card design should be minimalist, should communicate loyalty and stability, should be easy to read and clearly explain what we do. We have asked for front and back. However, the back of the card does not have to include much information at all. It could be just a small design, or a repeat of our phone number. Up to you. The attached file only says what is required on the card. It does not specify where to arrange the text, what fonts to use, etc etc. As much as we would like to give you more info, due to our very limited design ability, we are not really able to send you any rough, or otherwise, designs of what we are after. Hopefully the above description is enough for you.

```html
<!DOCTYPE html>
<html lang="en">
<head>
<meta charset="utf-8">
<title>Clearline Link – Business Card</title>
<link rel="stylesheet" href="https://fonts.googleapis.com/css2?family=Mulish:wght@400;700;800&family=Didact+Gothic&display=swap">
<style>
  :root {
    --backdrop: #d6d6d6;
    --card-white: #f8f8f8;
    --brand-blue: #0986ae;
    --brand-orange: #ef7d0f;
    --ink-grey: #555555;
    --rule-grey: #b5b5b5;
  }
  * { box-sizing: border-box; margin: 0; padding: 0; }
  html, body { width: 1200px; height: 960px; overflow: hidden; }
  body {
    background: var(--backdrop);
    position: relative;
    font-family: "Mulish", sans-serif;
  }
  .card {
    position: absolute;
    left: 320px;
    width: 600px;
    height: 342px;
    box-shadow: 0 3px 8px rgba(0,0,0,0.25);
  }
  .card--front { top: 100px; background: var(--card-white); }
  .card--back { top: 493px; background: var(--brand-blue); }

  .wordmark {
    position: absolute;
    left: 0; right: 0;
    text-align: center;
    font-family: "Mulish", sans-serif;
    font-weight: 800;
    font-size: 54px;
    letter-spacing: -0.5px;
    line-height: 1;
    white-space: nowrap;
  }
  .card--front .wordmark { top: 112px; color: var(--brand-blue); }
  .card--back .wordmark { top: 144px; color: #ffffff; }

  .identity {
    position: absolute;
    right: 348px;
    top: 218px;
    text-align: right;
    white-space: nowrap;
  }
  .identity__name {
    font-weight: 800;
    font-size: 19px;
    letter-spacing: 1px;
    color: var(--brand-blue);
    line-height: 22px;
  }
  .identity__role {
    font-family: "Didact Gothic", sans-serif;
    font-size: 15px;
    letter-spacing: 0.5px;
    color: var(--brand-orange);
    line-height: 20px;
  }
  .divider {
    position: absolute;
    left: 269px;
    top: 212px;
    width: 1px;
    height: 58px;
    background: var(--rule-grey);
  }
  .contacts {
    position: absolute;
    left: 286px;
    top: 212px;
    list-style: none;
    font-family: "Didact Gothic", sans-serif;
    font-size: 14.5px;
    color: var(--ink-grey);
    white-space: nowrap;
  }
  .contacts li {
    display: flex;
    align-items: center;
    height: 19px;
  }
  .contacts svg {
    width: 12px;
    height: 12px;
    margin-right: 10px;
    fill: var(--brand-blue);
    flex: none;
  }
</style>
</head>
<body>
  <section class="card card--front" aria-label="Business card front">
    <h1 class="wordmark">Clearline Link</h1>
    <div class="identity">
      <p class="identity__name">MILES HARCOURT</p>
      <p class="identity__role">CEO/FOUNDER</p>
    </div>
    <div class="divider"></div>
    <ul class="contacts">
      <li>
        <svg viewBox="0 0 12 12" aria-hidden="true"><path d="M2.4 0.6 L4.2 2.8 L3.2 4.2 C3.8 5.7 6.3 8.2 7.8 8.8 L9.2 7.8 L11.4 9.6 L10.2 11.3 C6.2 11.6 0.4 5.8 0.7 1.8 Z"/></svg>
        0491570156
      </li>
      <li>
        <svg viewBox="0 0 12 12" aria-hidden="true"><path d="M0.5 2.5 H11.5 V10 H0.5 Z M1.2 3.2 L6 6.8 L10.8 3.2" stroke="#fff" stroke-width="0.9"/></svg>
        miles@clearlinelink.com.au
      </li>
      <li>
        <svg viewBox="0 0 12 12" aria-hidden="true"><circle cx="6" cy="6" r="5.5"/><path d="M3 3.5 C4.5 3 5 4.5 4 5.5 C3.2 6.3 4.5 7.5 5 8.5 M7.5 2 C7 3.5 8.5 4 9.5 4.5 M8 7 C8.8 7.8 8.5 9 7.8 9.6" stroke="#fff" stroke-width="0.9" fill="none"/></svg>
        www.clearlinelink.com.au
      </li>
    </ul>
  </section>

  <section class="card card--back" aria-label="Business card back">
    <p class="wordmark">Clearline Link</p>
  </section>
</body>
</html>
```